VORLAND COMPOSITES INC website in USA

VORLAND COMPOSITES INC incorporated and operated in USA needs a completely new design of website. This Wyoming based company is a importer and distributor of composites material to supply mainly to American and Canadian/Mexican customers. Our main products includes Carbon Fiber, Aramid Fiber, Glass Fiber, Basalt Fiber, High Silica Glass, Quartz Fiber, S-Glass, Alumina Fiber, Vacuum Auxiliary.

We are one stop composites solution provider for Automotive, Aerospace, Construction, Electrical and Machinery industries.

We are exclusive sales company in North America for BLORAN composites produced from China and their other Asia facilities.

Target Market(s)

USA and Canada

Industry/Entity Type

Composites materials

Coding

Coded - Design and coding required

Number of Pages Required

5+ page

Requirements
Nice to have
• Color theme to match our corporate logo VORLAND. VORLAND stands for Northgate Provisioning Trade Holdings

```html
<!DOCTYPE html>
<html lang="en">
<head>
<meta charset="UTF-8">
<title>VORLAND COMPOSITES — Advanced Composite Materials</title>
<link href="https://fonts.googleapis.com/css2?family=Montserrat:wght@500;600;700&family=Open+Sans:wght@400;600;700&display=swap" rel="stylesheet">
<style>
:root{
  --navy:#14213d;
  --navy-deep:#0e1a30;
  --gold:#b8892f;
  --gold-bright:#c99a3a;
  --ink:#1d2538;
  --muted:#5b6473;
  --soft:#f4f6f9;
  --white:#ffffff;
  --line:#e4e7ec;
}
*{margin:0;padding:0;box-sizing:border-box}
html,body{width:1200px;height:1200px;overflow:hidden}
body{background:var(--white);font-family:"Open Sans",sans-serif;color:var(--ink)}
.site{width:1200px;height:1200px;overflow:hidden;display:flex;flex-direction:column}

.nav{height:80px;flex:none;display:flex;align-items:center;padding:0 74px;background:var(--white);box-shadow:0 1px 6px rgba(0,0,0,.06);position:relative;z-index:2}
.brand{display:flex;align-items:center;gap:10px;font-family:"Montserrat",sans-serif;font-weight:700;font-size:26px;color:var(--navy);letter-spacing:.3px}
.brand-mark{width:20px;height:20px;border-radius:50%;background:var(--gold)}
.nav-links{display:flex;gap:30px;margin-left:auto;font-family:"Montserrat",sans-serif;font-size:15px;font-weight:500;color:var(--navy);list-style:none}
.nav-links .active{color:var(--gold)}
.partner-pill{margin-left:46px;border:1.5px solid var(--navy);border-radius:16px;padding:5px 12px;font-family:"Montserrat",sans-serif;font-size:12px;font-weight:600;color:var(--navy)}

.hero{height:580px;flex:none;position:relative;overflow:hidden}
.hero-photo{position:absolute;inset:0;background:radial-gradient(ellipse at 78% 55%,#2a3548 0%,#1a2437 35%,transparent 70%),linear-gradient(100deg,#13203a 0%,#1b2840 55%,#1f2a3c 100%)}
.hero-content{position:relative;padding:140px 74px 0;max-width:720px;color:var(--white)}
.hero h1{font-family:"Montserrat",sans-serif;font-weight:700;font-size:52px;line-height:1.12}
.hero p{margin-top:30px;font-size:18px;line-height:1.6;color:#e6e9ef;max-width:580px}
.hero p strong{font-weight:700;color:var(--white)}
.hero-actions{display:flex;gap:16px;margin-top:44px}
.btn{font-family:"Montserrat",sans-serif;font-weight:600;font-size:15px;padding:14px 28px;border-radius:4px}
.btn-gold{background:var(--gold);color:var(--white)}
.btn-outline{border:2px solid var(--white);color:var(--white)}

.partnership{height:270px;flex:none;background:var(--soft);text-align:center;padding-top:72px}
.section-title{font-family:"Montserrat",sans-serif;font-weight:700;font-size:38px;color:var(--navy)}
.section-lead{margin:22px auto 0;max-width:760px;font-size:17px;line-height:1.6;color:var(--muted)}
.section-lead em{color:var(--gold);font-weight:700}

.products{flex:1;background:var(--white);text-align:center;padding-top:72px}
.cards{display:grid;grid-template-columns:repeat(3,330px);gap:36px;justify-content:center;margin-top:48px}
.card{background:var(--white);border-top:3px solid var(--gold);box-shadow:0 4px 18px rgba(20,33,61,.08);border-radius:4px;padding:40px 24px 30px}
.card svg{width:48px;height:48px}
.card h3{font-family:"Montserrat",sans-serif;font-weight:700;font-size:22px;color:var(--navy);margin-top:26px}
.card p{margin-top:14px;font-size:15px;color:var(--muted);line-height:1.5}
</style>
</head>
<body>
<div class="site">
  <header class="nav">
    <div class="brand"><span class="brand-mark"></span>VORLAND COMPOSITES</div>
    <ul class="nav-links">
      <li class="active">Home</li><li>Products</li><li>Industries</li><li>About</li><li>Contact</li>
    </ul>
    <span class="partner-pill">BLORAN Partner</span>
  </header>

  <section class="hero">
    <div class="hero-photo" role="img" aria-label="Dark blue photo of an engineer working at monitors with code on screen"></div>
    <div class="hero-content">
      <h1>Advanced Composite Materials for North America</h1>
      <p>Exclusive distributor for <strong>BLORAN</strong> high-performance fibers. Shaping the future with cutting-edge composite solutions for Automotive, Aerospace, Construction, and beyond.</p>
      <div class="hero-actions">
        <span class="btn btn-gold">Explore Products</span>
        <span class="btn btn-outline">Contact Our Experts</span>
      </div>
    </div>
  </section>

  <section class="partnership">
    <h2 class="section-title">Exclusive North American Partnership</h2>
    <p class="section-lead">We are the proud exclusive sales partner in North America for <em>BLORAN Composites</em>, leveraging their global manufacturing excellence to supply the highest quality materials.</p>
  </section>

  <section class="products">
    <h2 class="section-title">Our Core Product Lines</h2>
    <p class="section-lead">A comprehensive portfolio of advanced composite materials for demanding applications across industries.</p>
    <div class="cards">
      <article class="card">
        <svg viewBox="0 0 48 48" fill="none" stroke="#b8892f" stroke-width="3"><ellipse cx="24" cy="24" rx="20" ry="8"/><ellipse cx="24" cy="24" rx="20" ry="8" transform="rotate(60 24 24)"/><ellipse cx="24" cy="24" rx="20" ry="8" transform="rotate(120 24 24)"/><circle cx="24" cy="24" r="3" fill="#b8892f"/></svg>
        <h3>Carbon Fiber</h3>
        <p>Ultra high-strength material for lightweight structures</p>
      </article>
      <article class="card">
        <svg viewBox="0 0 48 48"><path d="M24 4 L40 10 V22 C40 33 33 41 24 44 C15 41 8 33 8 22 V10 Z" fill="#b8892f"/><path d="M24 9 V39 C17 36 13 30 13 22 V13 Z" fill="#fff"/></svg>
        <h3>Aramid Fiber</h3>
        <p>Exceptional impact resistance and thermal stability</p>
      </article>
      <article class="card">
        <svg viewBox="0 0 48 48"><path d="M8 6 H40 L36 42 H12 Z" fill="#b8892f"/><rect x="13" y="11" width="22" height="9" fill="#fff"/></svg>
        <h3>Glass Fiber</h3>
        <p>Versatile and cost-effective reinforcement</p>
      </article>
    </div>
  </section>
</div>
</body>
</html>
```